Nona's Brivelo

I am looking to design a label to be used on a glass jar for packaging a very special spice that has been used in our family for generations. The spice is excellent on meats, burgers, poultry, fish, and more.

The name of the spice is "Nona's Famous Brivelo"

Design should be traditional, with an Italian feel.

Total circumference of the jar is 10"
Height of jar is 4"

Some of the glass should not be covered to reveal color of spice inside.

Target Market(s)

Female 25-75

```html
<!DOCTYPE html>
<html lang="en">
<head>
<meta charset="utf-8">
<title>Nona's Brivelo – Special Seasoning Label</title>
<link href="https://fonts.googleapis.com/css2?family=Arimo:wght@400&family=Tinos:wght@400;700&display=swap" rel="stylesheet">
<style>
  :root {
    --paper: #ffffff;
    --band-green: #07993f;
    --band-red: #d0321a;
    --band-black: #111111;
    --oval-green: #0b4a3a;
    --frame-red: #d0321a;
    --wedge-red: #ff0000;
    --wedge-green: #3f8f33;
    --ribbon-dark: #0a5e30;
    --ribbon-light: #4fae1e;
    --ink: #ffffff;
    --pill: #1a1a1a;
    --art-tone: #f3efe8;
  }
  html, body {
    margin: 0;
    padding: 0;
    width: 1200px;
    height: 929px;
    overflow: hidden;
    background: var(--paper);
  }
  .label {
    display: block;
    width: 1200px;
    height: 929px;
  }
  .brand-name {
    font-family: "Tinos", "Times New Roman", serif;
    font-size: 66px;
    fill: var(--ink);
  }
  .usage-line {
    font-family: "Arimo", Arial, sans-serif;
    font-size: 21px;
    fill: var(--ink);
  }
  .banner-title {
    font-family: "Tinos", "Times New Roman", serif;
    fill: var(--ink);
    stroke: #0b0b0b;
    stroke-width: 3px;
    paint-order: stroke fill;
    text-anchor: middle;
  }
  .banner-title--top { font-size: 80px; }
  .banner-title--bottom { font-size: 62px; }
  .net-weight {
    font-family: "Arimo", Arial, sans-serif;
    font-size: 22px;
    fill: var(--ink);
    text-anchor: middle;
  }
</style>
</head>
<body>
<svg class="label" viewBox="0 0 1163 900" preserveAspectRatio="none" xmlns="http://www.w3.org/2000/svg">
  <defs>
    <linearGradient id="ribbon-sheen" x1="0" x2="1" y1="0" y2="0">
      <stop offset="0" stop-color="var(--ribbon-dark)"/>
      <stop offset="0.55" stop-color="var(--ribbon-light)"/>
      <stop offset="1" stop-color="var(--ribbon-dark)"/>
    </linearGradient>
    <clipPath id="window-clip">
      <ellipse cx="583" cy="440" rx="305" ry="345"/>
    </clipPath>
    <!-- name runs on an ellipse centred on the window, just outside the red ring -->
    <path id="name-arc" d="M 255,440 A 328 374 0 0 1 911,440"/>
    <!-- taglines run on the green ring, baseline just outside the red ring -->
    <path id="usage-arc" d="M 299,615 A 324 364 0 1 1 867,615"/>
  </defs>

  <!-- wrap bands -->
  <g class="wrap-band">
    <rect x="0" y="172" width="1163" height="18" fill="var(--band-red)"/>
    <rect x="0" y="190" width="1163" height="7" fill="var(--band-black)"/>
    <rect x="0" y="197" width="1163" height="515" fill="var(--band-green)"/>
    <rect x="0" y="712" width="1163" height="8" fill="var(--band-black)"/>
    <rect x="0" y="720" width="1163" height="25" fill="var(--band-red)"/>
  </g>

  <!-- oval badge -->
  <g class="badge">
    <ellipse cx="583" cy="452" rx="390" ry="447" fill="var(--oval-green)"/>
    <ellipse cx="583" cy="440" rx="312" ry="352" fill="var(--paper)" stroke="var(--frame-red)" stroke-width="6"/>
    <g class="badge-window" clip-path="url(#window-clip)">
      <polygon points="270,285 345,285 520,650 270,650" fill="var(--wedge-red)"/>
      <polygon points="830,285 900,285 900,650 655,650" fill="var(--wedge-green)"/>
      <rect class="mascot-art" role="img" aria-label="Illustration of a smiling grandmother with glasses and a hair bun"
            x="455" y="160" width="265" height="430" rx="110" fill="var(--art-tone)"/>
    </g>

    <text class="brand-name"><textPath href="#name-arc" startOffset="50%" text-anchor="middle">Nona's Brivelo</textPath></text>
    <text class="usage-line"><textPath href="#usage-arc" startOffset="0.5%">Excellent on meats, burgers, fish</textPath></text>
    <text class="usage-line"><textPath href="#usage-arc" startOffset="99.5%" text-anchor="end">Excellent on poultry, and more</textPath></text>
  </g>

  <!-- ribbon banner -->
  <g class="ribbon">
    <polygon class="ribbon-tail" points="305,680 205,690 248,755 215,832 305,792" fill="url(#ribbon-sheen)" stroke="var(--frame-red)" stroke-width="4"/>
    <polygon class="ribbon-tail" points="860,680 962,690 918,755 950,832 860,792" fill="url(#ribbon-sheen)" stroke="var(--frame-red)" stroke-width="4"/>
    <path class="ribbon-face" d="M 295,610 Q 583,548 870,610 L 870,785 Q 583,742 295,785 Z"
          fill="url(#ribbon-sheen)" stroke="var(--frame-red)" stroke-width="4"/>
    <text class="banner-title banner-title--top" x="583" y="672">SPECIAL</text>
    <text class="banner-title banner-title--bottom" x="583" y="748">SEASONING</text>
  </g>

  <!-- net weight -->
  <g class="net-weight-tag">
    <rect x="477" y="814" width="208" height="40" rx="20" fill="var(--pill)"/>
    <text class="net-weight" x="581" y="842">Net Wt. 1.75 oz</text>
  </g>
</svg>
</body>
</html>
```